Residential Mortgage Leader needs Wordpress Design

Looking for a home page website design for a client. We develop using the WordPress platform and would prefer the design be at least loosely based on an existing WordPress template. Attached files have many notes from our creative brief with client. The site must be responsive. Approved, basic wireframe attached. There is room for interpretation.

Existing web site: http://www.marisolkettering.example/

The Marisol Kettering Team relies on strong systems to deliver an on-time, done-right, friendly experience. Marisol offers mortgages and refinancing services throughout the United States. She is a successful Brookvale Funding agent who strives to be an active part of her community. She would like to focus the site on her team, rather than just her.

Difference makers...
When you work with the Marisol Kettering team you get a high level of expertise and a friendly experience.

She has amazing credentials. Marisol is widely recognized as a top producer for her company, and has earned a number of awards and honors for her customer service.

Marisol's team is very engaged and enjoys sharing social comments or photos from their community.

Imagery:
* Friendly, warm imagery, preferably of her team or an image to represent her team
* Clean and crisp
* Professional / Experts in mortgage and refinance
* Clean / Good use of white space
Updates

When possible, please use imagery from the DFW area. The client mentioned they would prefer not to see stock images. Thanks.

Amend that- creative use of stock images, however, is fine. A few designs have used stock imagery, but in a well-considered manner.

We added some photos and graphics that are local. We are Dallas / Ft. Worth, Plano, Frisco, Texas. We also added some examples of photos to use for the "In the Community" area. Stock photos of business folks just doesn't fit there. Thanks!

Target Market(s)

They service a lot of builders, but also work with homeowners. Their typical client is usually a woman searching for mortgage services online. She typically has a family and may refer her husband to Marisol's team. Keep in mind, however, they also see a number of other scenarios. Most of their clients are middle to high-end borrowers.

Industry/Entity Type

It Company

Requirements
Must have
• Design should be developed using program such as Photoshop or Fireworks or Illustrator as last preference. Ideally, the design would be based on an existing responsive WordPress theme, which we would customize. You must include the name of the target theme. The footer should include lots of space for disclaimers and legal language. Site navigation should include these choices: "Home, About, Builders, Mortgage Info, Approval, Blog, Contact"
Nice to have
• Blog, social media and photos area. Use of the already approved style prototype with colors and fonts (Lato- a Google font, Times New Roman and Cookie-a decorative Google font). However, we are open to interpretation.
Should not have
• Hard to read fonts or a lack of white space.

```html
<!DOCTYPE html>
<html lang="en">
<head>
<meta charset="utf-8">
<title>Brookvale Funding – Marisol Kettering Team</title>
<link rel="stylesheet" href="https://fonts.googleapis.com/css2?family=Lato:wght@300;400;700&display=swap">
<style>
:root{
  --red:#c0311f;
  --red-bright:#d0160f;
  --dark:#262626;
  --band:#454546;
  --footer:#353535;
  --page:#f4f3f1;
  --text:#333;
  --blue:#1a8bbf;
  --card:#eeeeee;
  --line:#dcdcdc;
}
*{box-sizing:border-box;margin:0;padding:0}
html,body{width:889px;height:1200px;overflow:hidden;background:var(--page)}
body{font-family:'Lato',sans-serif;color:var(--text)}
.canvas{position:relative;width:889px;height:1200px;overflow:hidden;background:var(--page)}
.abs{position:absolute}

.topbar{left:0;top:0;width:889px;height:32px;background:var(--dark);color:#fff;font-size:9.5px;text-align:center;line-height:30px}
.topbar a{color:var(--red-bright);text-decoration:none}

.brand{left:88px;top:46px}
.brand-name{font-size:20px;font-weight:700;color:var(--red);letter-spacing:-0.3px;line-height:22px}
.brand-sub{font-size:9.5px;color:#555;line-height:12px;margin-top:2px}
.brand-mark{display:inline-block;width:13px;height:13px;border-radius:50%;background:var(--red);margin-left:6px;vertical-align:1px}

.search{left:661px;top:52px;width:141px;height:26px;background:#fff;border:1px solid #e0e0e0;font-size:9px;color:#aaa;padding:0 8px;line-height:24px}
.search svg{position:absolute;right:6px;top:6px}

.nav{left:0;top:110px;width:889px;height:24px;border-bottom:1px solid var(--line)}
.nav a{position:absolute;top:2px;font-size:11px;font-weight:300;color:#444;text-decoration:none}
.nav a.current{color:var(--red)}

.hero{left:74px;top:167px;width:741px;height:408px;box-shadow:0 0 6px rgba(0,0,0,.25);
  background:
    linear-gradient(90deg,rgba(196,160,120,.55) 0%,rgba(150,140,110,.45) 45%,rgba(150,140,110,0) 55%),
    linear-gradient(180deg,#a9c0d8 0%,#dfe5ea 22%,#c9bdb0 42%,#a99484 60%,#7b9a44 80%,#56782a 100%)}

.band{left:0;top:574px;width:889px;height:173px;background:var(--band)}
.band h2{left:88px;top:22px;font-size:17px;font-weight:700;color:#fff;text-transform:uppercase}
.band p{left:89px;top:54px;width:450px;font-size:11.2px;line-height:20.5px;color:#f1f1f1;font-weight:400}
.btn{left:89px;top:131px;width:89px;height:21px;background:var(--red-bright);border-radius:2px;color:#fff;font-size:11px;line-height:21px;padding-left:7px}
.btn svg{position:absolute;right:7px;top:7px}

.feature{left:566px;width:236px;background:var(--red);color:#fff;text-align:center}
.feature h3{font-size:17px;font-weight:400;margin-bottom:7px}
.feature p{font-size:8.3px;line-height:16.5px;padding:0 12px;font-weight:300}
.awards{top:404px;height:170px;padding-top:10px}
.recog{top:575px;height:172px;padding-top:13px;border-top:1px solid #a9271a}

.tab{top:777px;height:21px;color:#fff;font-size:13px;text-align:center;line-height:22px;text-transform:uppercase}
.tab-blog{left:88px;width:235px;background:var(--red-bright)}
.tab-social{left:328px;width:235px;background:#303030}
.tab-community{left:567px;width:235px;background:var(--blue)}

.thumb{width:57px;height:57px}
.thumb-book{background:linear-gradient(180deg,#6b3a20 0%,#7e4524 30%,#e8d8bc 55%,#d2ad7c 75%,#8b5a2c 100%)}
.post-title{font-size:10.5px;color:#333;margin-bottom:4px}
.post-text{font-size:8.3px;line-height:12px;color:#333;width:125px}
.divider{left:320px;top:814px;width:1px;height:129px;background:#cfcfcf}
.marker{left:317px;top:824px;width:3px;height:20px;background:var(--red-bright)}

.social-card{left:328px;width:235px;height:57px;background:var(--card)}
.social-card .thumb{position:absolute;left:0;top:0}
.social-card p{position:absolute;left:70px;top:16px;width:145px;font-size:8.3px;line-height:12px}
.thumb-couple{background:linear-gradient(180deg,#f4f0ea 0%,#e2c4a4 55%,#c9a27c 100%)}
.thumb-desk{background:linear-gradient(180deg,#6a87a8 0%,#39567a 50%,#e6ebf0 100%)}

.community-text{left:569px;top:820px;width:115px;font-size:8.5px;line-height:17px;color:#444}
.community-photo{left:691px;top:813px;width:110px;height:130px;background:linear-gradient(90deg,#a8d3f0 0%,#c9a672 30%,#a07645 55%,#3f76b0 80%,#6ea2d6 100%)}

.footer{left:0;top:974px;width:889px;height:190px;background:var(--footer);color:#aaa}
.f-brand{left:89px;top:24px}
.f-brand .brand-name{color:#8a8a8a;font-size:15px;line-height:18px}
.f-brand .brand-sub{color:#8a8a8a;font-size:7px}
.f-brand .brand-mark{background:#8a8a8a;width:10px;height:10px}
.f-about{left:89px;top:68px;width:230px;font-size:8.6px;line-height:19.6px;color:#a8a8a8}
.f-links{left:367px;top:20px}
.f-links h4{font-size:13px;font-weight:400;color:#e6e6e6;margin-bottom:7px}
.f-links a{display:block;font-size:8.6px;line-height:19.6px;color:#a8a8a8;text-decoration:none}
.agent-photo{left:531px;top:16px;width:135px;height:158px;background:linear-gradient(180deg,#6d5546 0%,#8a6a56 40%,#3a2d28 75%,#2a2624 100%)}
.agent{left:681px;top:14px}
.agent h4{font-size:13px;font-weight:400;color:#fff;line-height:17px;margin-bottom:8px}
.agent p{font-size:8.6px;line-height:19.6px;color:#a8a8a8}

.bottom{left:0;top:1164px;width:889px;height:36px;background:var(--page)}
.copy{left:88px;top:14px;font-size:7.5px;color:#222}
.social-dot{top:12px;width:13px;height:13px;border-radius:50%;background:#d4d4d4}
</style>
</head>
<body>
<div class="canvas">

  <div class="abs topbar">Welcome to the Marisol Kettering Team at Brookvale Funding. <a href="#">read more</a></div>

  <div class="abs brand">
    <div class="brand-name">Brookvale Funding<span class="brand-mark"></span></div>
    <div class="brand-sub">A Harborline Company</div>
  </div>

  <div class="abs search">Search
    <svg width="12" height="12" viewBox="0 0 12 12"><circle cx="5" cy="5" r="3.5" fill="none" stroke="#d0160f" stroke-width="1.8"/><line x1="7.6" y1="7.6" x2="11" y2="11" stroke="#d0160f" stroke-width="2"/></svg>
  </div>

  <nav class="abs nav">
    <a class="current" href="#" style="left:89px">Home</a>
    <a href="#" style="left:158px">About</a>
    <a href="#" style="left:229px">Builders</a>
    <a href="#" style="left:309px">Mortage Info</a>
    <a href="#" style="left:411px">Approval Blog</a>
    <a href="#" style="left:518px">Contact Info</a>
  </nav>

  <div class="abs hero" role="img" aria-label="Smiling couple in front of a two-storey brick house with a green lawn under a blue sky"></div>

  <section class="abs band">
    <h2 class="abs">Our Credentials</h2>
    <p class="abs">Lorem Ipsum is simply dummy text of the printing and typesetting industry. Lorem Ipsum has been the industry's standard dummy text ever since the 1500s, when an unknown printer took a galley of type and scrambled it to make a type specimen book.</p>
    <div class="abs btn">Read more
      <svg width="6" height="7" viewBox="0 0 6 7"><polygon points="0,0 6,3.5 0,7" fill="#f3b0a8"/></svg>
    </div>
  </section>

  <div class="abs feature awards">
    <svg width="56" height="62" viewBox="0 0 56 62">
      <polygon points="18,34 8,54 16,52 20,60 28,40" fill="#fff"/>
      <polygon points="38,34 48,54 40,52 36,60 28,40" fill="#fff"/>
      <circle cx="28" cy="24" r="22" fill="#fff"/>
      <circle cx="28" cy="24" r="15" fill="none" stroke="#c0311f" stroke-width="1" stroke-dasharray="2 2"/>
    </svg>
    <h3>Awards</h3>
    <p>Lorem Ipsum is simply dummy text of the printing and typesetting industry. Lorem Ipsum has been the industry's standard dummy text ever.</p>
  </div>

  <div class="abs feature recog">
    <svg width="44" height="58" viewBox="0 0 44 58">
      <rect x="2" y="2" width="40" height="54" rx="7" fill="#fff"/>
      <rect x="8" y="8" width="28" height="42" rx="3" fill="#c0311f"/>
      <circle cx="22" cy="29" r="10" fill="none" stroke="#fff" stroke-width="2.5"/>
      <g stroke="#fff" stroke-width="2"><line x1="22" y1="19" x2="22" y2="39"/><line x1="12" y1="29" x2="32" y2="29"/><line x1="15" y1="22" x2="29" y2="36"/><line x1="29" y1="22" x2="15" y2="36"/></g>
    </svg>
    <h3>Recognitions</h3>
    <p>Lorem Ipsum is simply dummy text of the printing and typesetting industry. Lorem Ipsum has been the industry's standard dummy text ever.</p>
  </div>

  <div class="abs tab tab-blog">Blog</div>
  <div class="abs tab tab-social">Socials</div>
  <div class="abs tab tab-community">In the Community</div>

  <div class="abs thumb thumb-book" style="left:89px;top:814px" role="img" aria-label="Open book on a library shelf"></div>
  <div class="abs" style="left:157px;top:820px">
    <div class="post-title">Borrwoing</div>
    <div class="post-text">Lorem Ipsum is simply dummy text of the and typesetting.</div>
  </div>
  <div class="abs thumb thumb-book" style="left:89px;top:886px" role="img" aria-label="Open book on a library shelf"></div>
  <div class="abs" style="left:157px;top:892px">
    <div class="post-title">Best Practice</div>
    <div class="post-text">Lorem Ipsum is simply dummy text of the and typesetting.</div>
  </div>

  <div class="abs divider"></div>
  <div class="abs marker"></div>

  <div class="abs social-card" style="top:814px">
    <div class="thumb thumb-couple" role="img" aria-label="Smiling couple portrait"></div>
    <p>Lorem Ipsum is simply dummy text of the and typesetting. industry.</p>
  </div>
  <div class="abs social-card" style="top:886px">
    <div class="thumb thumb-desk" role="img" aria-label="People working at a laptop"></div>
    <p>Lorem Ipsum is simply dummy text of the and typesetting. industry.</p>
  </div>

  <div class="abs community-text">Lorem Ipsum is simply dummy text of the printing and typesetting industry. Lorem Ipsum has been the industry's standard dummy text ever since the 1500s, when an unknown.</div>
  <div class="abs community-photo" role="img" aria-label="Curved modern building facade against blue sky"></div>

  <footer class="abs footer">
    <div class="abs f-brand">
      <div class="brand-name">Brookvale Funding<span class="brand-mark"></span></div>
      <div class="brand-sub">A Harborline Company.</div>
    </div>
    <p class="abs f-about">Lorem Ipsum is simply dummy text of the printing and typesetting industry. Lorem Ipsum has been the industry's standard dummy text ever since the 1500s, when an unknown printer took a galley of type and scrambled it to make a type specimen book.</p>
    <div class="abs f-links">
      <h4>Quick Link</h4>
      <a href="#">Home</a><a href="#">About</a><a href="#">Builders</a><a href="#">Mortagage Info</a><a href="#">Approval Blogs</a><a href="#">Contact us</a>
    </div>
    <div class="abs agent-photo" role="img" aria-label="Portrait of the branch manager"></div>
    <div class="abs agent">
      <h4>Marisol Kettering,<br>Branch Manager</h4>
      <p>Office: 555.014.2200</p>
      <p>Cell: 555.018.3310</p>
      <p>mkettering@brookvale.example</p>
      <p>NMLS: 10492</p>
      <p>4820 Linden Court , Ste. 210</p>
      <p>Cedar Hollow, TX 75999</p>
    </div>
  </footer>

  <div class="abs bottom">
    <div class="abs copy">Copyright © Brookvale Funding. All Rights Reserved.</div>
    <span class="abs social-dot" style="left:736px" aria-label="Social link"></span>
    <span class="abs social-dot" style="left:762px" aria-label="Social link"></span>
    <span class="abs social-dot" style="left:787px" aria-label="Social link"></span>
  </div>

</div>
</body>
</html>
```